Business Card Design for Marketing Firm

Looking for business card design for higher end marketing firm. Clean but impressionable/trendy. We are a marketing firm that represents manufacturers in the foodservice equipment and supply industry. Our customers are end users such has hotels, restaurants, country clubs, convention centers and casinos as well as distributors of restaurants supplies and equipment, and manufacturers of foodservice equipment and supplies.
Target Market(s)
Hotels, Restaurants, Supply & Equipment Distributors, Foodservice Manufacturers
Industry/Entity Type
Foodservice/Hospitality
Contact Information for Business Card
Name, Title, Contact Number, Email, Website, Social Media, Address
Requirements
Must have
- Clean & Simple but Serious and Impressionable

```html
<!DOCTYPE html>
<html lang="en">
<head>
<meta charset="utf-8">
<title>Meridian Hospitality Reps – Business Card</title>
<link rel="stylesheet" href="https://fonts.googleapis.com/css2?family=Noto+Serif:wght@400;700&family=Arimo:wght@400&display=swap">
<style>
  :root {
    --backdrop: #1e1e1f;
    --card-white: #f4f4f4;
    --navy: #272b6b;
    --ink: #2f2f33;
    --on-navy: #ffffff;
  }
  * { margin: 0; padding: 0; box-sizing: border-box; }
  html, body { width: 1200px; height: 1059px; overflow: hidden; }
  body {
    background: var(--backdrop);
    position: relative;
    font-family: "Arimo", Arial, sans-serif;
  }
  .card {
    position: absolute;
    width: 690px;
    height: 392px;
    border-radius: 20px;
    overflow: hidden;
  }
  .card--front { left: 256px; top: 89px; background: var(--card-white); }
  .card--back  { left: 255px; top: 548px; background: var(--navy); }

  .brand {
    position: absolute;
    transform: translateX(-50%);
    display: flex;
    flex-direction: column;
    align-items: center;
  }
  .card--front .brand { left: 190px; top: 130px; color: var(--navy); }
  .card--back  .brand { left: 345px; top: 100px; color: var(--on-navy); }

  .brand-mark {
    border-radius: 50%;
    background: currentColor;
  }
  .card--front .brand-mark { width: 74px; height: 74px; margin-bottom: 16px; }
  .card--back  .brand-mark { width: 104px; height: 104px; margin-bottom: 30px; }

  .brand-name {
    display: inline-block;
    font-family: "Noto Serif", Georgia, serif;
    font-weight: 400;
    text-transform: uppercase;
    letter-spacing: 0.04em;
    line-height: 1;
    white-space: nowrap;
  }
  .brand-name .line-end { display: block; text-align: right; }
  .card--front .brand-name { font-size: 20px; }
  .card--back  .brand-name { font-size: 33px; }
  .card--front .brand-name .line-end { margin-top: 2px; }
  .card--back  .brand-name .line-end { margin-top: 3px; }

  .divider {
    position: absolute;
    left: 344px; top: 114px;
    width: 1.5px; height: 152px;
    background: var(--navy);
  }

  .person { position: absolute; left: 375px; top: 108px; }
  .person__name {
    font-family: "Noto Serif", Georgia, serif;
    font-weight: 700;
    font-size: 24px;
    color: var(--navy);
    letter-spacing: 0.01em;
    white-space: nowrap;
  }
  .person__title { font-size: 16px; color: var(--ink); margin-top: 1px; }

  .contact-list {
    position: absolute; left: 375px; top: 177px;
    list-style: none;
  }
  .contact-list li {
    display: flex; align-items: center;
    height: 23.6px;
    font-size: 16px;
    color: var(--ink);
    white-space: nowrap;
  }
  .contact-list svg { width: 12px; height: 12px; margin-right: 7px; fill: var(--ink); }
  .contact-list .no-icon { padding-left: 19px; }

  .address-band {
    position: absolute;
    left: 0; right: 0; top: 328px;
    height: 32px;
    background: var(--navy);
    color: var(--on-navy);
    font-size: 15px;
    display: flex; align-items: center; justify-content: center;
  }
</style>
</head>
<body>
  <section class="card card--front" aria-label="Business card front">
    <div class="brand">
      <div class="brand-mark" role="img" aria-label="Company mark"></div>
      <div class="brand-name">Meridian Hospitality<span class="line-end">Reps</span></div>
    </div>
    <div class="divider"></div>
    <div class="person">
      <h1 class="person__name">DANIEL WHITMORE</h1>
      <p class="person__title">CEO/Founder</p>
    </div>
    <ul class="contact-list">
      <li>
        <svg viewBox="0 0 12 12" aria-hidden="true"><path d="M1 4.5C1 3 3 2 6 2s5 1 5 2.5V5.5H8.5V4.2H3.5V5.5H1zM2.5 6.5h7l1 4H1.5z"/></svg>
        555-204-3817
      </li>
      <li>
        <svg viewBox="0 0 12 12" aria-hidden="true"><path d="M1 5l5-3.5L11 5v6H1zM2 5.6l4 2.8 4-2.8L6 2.8z"/></svg>
        hello@meridianhospitalityreps.com
      </li>
      <li>
        <svg viewBox="0 0 12 12" aria-hidden="true"><circle cx="6" cy="6" r="5"/><path d="M3 4.5l2-1 1 1.5-1.5 1.5L5 8.5 3.5 7z M7 7.5l2-0.5 0.5 1.5-2 1z" fill="#f4f4f4"/></svg>
        www.meridianhospitalityreps.com
      </li>
      <li class="no-icon">@meridianhospitalityreps</li>
    </ul>
    <div class="address-band">450 Harbor Avenue, Suite 210 Lakeview, CA 90210</div>
  </section>

  <section class="card card--back" aria-label="Business card back">
    <div class="brand">
      <div class="brand-mark" role="img" aria-label="Company mark"></div>
      <div class="brand-name">Meridian Hospitality<span class="line-end">Reps</span></div>
    </div>
  </section>
</body>
</html>
```